Business Card Design Project

I require a business card with the following information on them for various different people;
name
m:
f:
e:
I have a logo already and will attached that. We are in the construction industry. I require something clean and simple but eye catching at the same time. You can use another colour with our logo if you like and you can style the logo as well if you wish. I am open.
Also it needs to be front and back design.
Industry/Entity Type
Construction
Requirements
Must have
- Logo, name, mobile, fax and email address.
Front and back design

```html
<!DOCTYPE html>
<html lang="en">
<head>
<meta charset="utf-8">
<title>Stonefield Developments – Business Card</title>
<link href="https://fonts.googleapis.com/css2?family=Questrial&family=Arimo&family=Archivo+Narrow&display=swap" rel="stylesheet">
<style>
  :root {
    --paper: #ffffff;
    --bleed: #0b0c0b;
    --lime: #8fe61f;
    --lime-bright: #86f01a;
    --forest: #13450c;
    --slate: #b3bdbc;
    --ink: #111111;
    --brand-grey: #5e676a;
    --trim: #000000;
  }
  html, body {
    margin: 0;
    padding: 0;
    width: 1200px;
    height: 887px;
    overflow: hidden;
    background: var(--paper);
  }
  .sheet {
    position: relative;
    width: 1200px;
    height: 887px;
  }
  .trim-mark { position: absolute; background: var(--trim); }
  .trim-mark.v { width: 1px; height: 121px; }
  .trim-mark.h { height: 1px; width: 121px; }

  .bleed-area {
    position: absolute;
    left: 153px; top: 152px;
    width: 895px; height: 581px;
    background: var(--bleed);
  }
  .card {
    position: absolute;
    left: 181px; top: 181px;
    width: 839px; height: 524px;
    background: var(--paper);
    border-radius: 42px;
    overflow: hidden;
  }
  .brand {
    position: absolute;
    left: 0; right: 0; top: 128px;
    display: flex;
    justify-content: center;
    align-items: center;
    gap: 16px;
  }
  .brand-mark {
    width: 38px; height: 38px;
    background: var(--lime);
  }
  .brand-name {
    font-family: "Questrial", sans-serif;
    font-size: 48px;
    color: var(--brand-grey);
    letter-spacing: 0.5px;
  }
  .person-name {
    position: absolute;
    left: 41px; top: 283px;
    margin: 0;
    font-family: "Arimo", sans-serif;
    font-weight: 400;
    font-size: 39px;
    color: var(--lime);
  }
  .name-rule {
    position: absolute;
    left: 0; top: 331px;
    width: 386px; height: 4px;
    background: linear-gradient(90deg, #111 0%, #1c3a10 60%, #2f5a12 100%);
  }
  .contact {
    position: absolute;
    display: flex;
    align-items: center;
    gap: 5px;
    font-family: "Archivo Narrow", sans-serif;
    font-size: 27px;
    color: var(--ink);
  }
  .contact svg { display: block; }
  .contact.mobile { left: 32px; top: 340px; }
  .contact.fax { left: 218px; top: 340px; }
  .contact.email { left: 30px; top: 373px; }

  .band { position: absolute; }
  .band-slate { left: 0; top: 0; }
</style>
</head>
<body>
<div class="sheet">
  <div class="trim-mark v" style="left:181px;top:0"></div>
  <div class="trim-mark v" style="left:1020px;top:0"></div>
  <div class="trim-mark v" style="left:181px;top:766px"></div>
  <div class="trim-mark v" style="left:1020px;top:766px"></div>
  <div class="trim-mark h" style="left:0;top:181px"></div>
  <div class="trim-mark h" style="left:0;top:705px"></div>
  <div class="trim-mark h" style="left:1079px;top:181px"></div>
  <div class="trim-mark h" style="left:1079px;top:705px"></div>

  <div class="bleed-area"></div>

  <div class="card">
    <div class="brand">
      <span class="brand-mark"></span>
      <span class="brand-name">Stonefield Developments</span>
    </div>

    <h1 class="person-name">Mark Hollis</h1>
    <div class="name-rule"></div>

    <div class="contact mobile">
      <svg width="16" height="26" viewBox="0 0 16 26" aria-hidden="true">
        <rect x="1" y="3" width="14" height="22" rx="3" fill="var(--lime)"/>
        <rect x="4" y="7" width="8" height="7" fill="#fff"/>
        <rect x="11" y="0" width="2" height="4" fill="var(--lime)"/>
      </svg>
      <span>0400 123 456</span>
    </div>
    <div class="contact fax">
      <svg width="28" height="26" viewBox="0 0 28 26" aria-hidden="true">
        <rect x="8" y="1" width="12" height="9" fill="none" stroke="var(--lime)" stroke-width="2"/>
        <rect x="2" y="9" width="24" height="15" rx="2" fill="var(--lime)"/>
        <rect x="13" y="13" width="9" height="7" fill="#fff"/>
        <rect x="5" y="12" width="5" height="10" fill="#5fa516"/>
      </svg>
      <span>03 9000 1234</span>
    </div>
    <div class="contact email">
      <svg width="26" height="20" viewBox="0 0 26 20" aria-hidden="true">
        <rect x="1" y="4" width="24" height="15" fill="none" stroke="var(--lime)" stroke-width="2"/>
        <path d="M1 4 L13 13 L25 4 M1 19 L10 11 M25 19 L16 11" fill="none" stroke="var(--lime)" stroke-width="2"/>
      </svg>
      <span>mark@stonefielddev.com.au</span>
    </div>

    <svg class="band band-slate" width="839" height="524" viewBox="0 0 839 524" aria-hidden="true">
      <polygon points="427,411 839,411 839,430 407,430" fill="var(--slate)"/>
      <rect x="0" y="430" width="839" height="34" fill="var(--forest)"/>
      <polygon points="89,464 839,464 839,480 105,480" fill="var(--lime-bright)"/>
    </svg>
  </div>
</div>
</body>
</html>
```